Young, dynamic furniture company needs a new business card design

We require a new business card design for our modern furniture company which supplies furniture and appliances to the property and development market.
Oakridge Interiors has become one of the leading furniture & appliance suppliers to the property market withing London. With over 10 years experience, we have increased our business to supply not only private landlords and managing agents, but also property developers, housing associations and local councils.
We offer not only a complete range of furniture which includes beds, wardrobes, dining sets and sofas, but also a high quality, full delivery and assembly service to help you with all our furnishing needs.

Target Market(s)

Private landlords, estate agents, letting agents, property management companies

Industry/Entity Type

Business

Contact Information for Business Card

Name,
Title,
Address,
Mobile,
Telephone,
Fax, Website, email address

Font styles to use
Sans Serif

Colors
3176b5
0555a3
85abd2
cfdeed

Requirements
Must have
• All the above information for each of our staff, along with our logo

```html
<!DOCTYPE html>
<html lang="en">
<head>
<meta charset="utf-8">
<title>Oakridge Interiors – Business Card</title>
<link href="https://fonts.googleapis.com/css2?family=Montserrat:wght@400;700&family=Roboto+Condensed:wght@400&display=swap" rel="stylesheet">
<style>
  :root {
    --page-bg: #d9d3cb;
    --panel-light-top: #f2f3f6;
    --panel-light-bottom: #e9e3e6;
    --navy-deep: #0d1d4a;
    --navy-mid: #1b2f6e;
    --navy-glow: #2a4289;
    --edge-dark: #15151c;
    --edge-silver: #b9bcc6;
    --gold: #c9ad86;
    --gold-soft: #d3c2a6;
    --muted-light: #c3c4cc;
    --brand-grey: #3b3b42;
  }
  * { margin: 0; padding: 0; box-sizing: border-box; }
  html, body { width: 1200px; height: 970px; overflow: hidden; background: var(--page-bg); }
  .canvas { position: relative; width: 1200px; height: 970px; }
  .card {
    position: absolute; left: 80px; top: 189px; width: 1040px; height: 592px;
    background: linear-gradient(180deg, var(--panel-light-top), var(--panel-light-bottom));
    box-shadow: 0 10px 30px rgba(0,0,0,.18); overflow: hidden;
  }
  .card-shape { position: absolute; inset: 0; }
  .brand { position: absolute; left: 30px; width: 440px; top: 385px; text-align: center; color: var(--brand-grey); font-family: "Roboto Condensed", sans-serif; }
  .brand-name { font-size: 40px; letter-spacing: .5px; text-transform: uppercase; line-height: 1; }
  .brand-tagline { font-size: 22px; text-transform: uppercase; margin-top: 8px; }
  .details { position: absolute; left: 575px; top: 100px; font-family: "Montserrat", sans-serif; }
  .person-name { font-size: 35px; font-weight: 700; color: var(--gold); letter-spacing: .5px; line-height: 1; }
  .person-title { font-size: 26px; color: var(--muted-light); line-height: 1.1; }
  .address { margin-top: 72px; font-size: 26px; color: var(--gold-soft); line-height: 38px; }
  .contacts { list-style: none; margin-top: 16px; }
  .contacts li { display: flex; align-items: center; height: 36.5px; font-size: 27px; color: var(--gold-soft); }
  .contact-icon { width: 30px; height: 30px; margin-right: 14px; flex: none; }
</style>
</head>
<body>
<div class="canvas">
  <div class="card">
    <svg class="card-shape" viewBox="0 0 1040 592" width="1040" height="592" aria-hidden="true">
      <defs>
        <linearGradient id="navy" x1="0" y1="0" x2="1" y2="1">
          <stop offset="0" stop-color="var(--navy-mid)"/>
          <stop offset=".55" stop-color="var(--navy-glow)"/>
          <stop offset="1" stop-color="var(--navy-deep)"/>
        </linearGradient>
      </defs>
      <path d="M478 0 C528 120 528 380 438 592 L450 592 C540 380 540 120 490 0 Z" fill="var(--edge-dark)"/>
      <path d="M490 0 C540 120 540 380 450 592 L458 592 C548 380 548 120 498 0 Z" fill="var(--edge-silver)"/>
      <path d="M498 0 C548 120 548 380 458 592 L1040 592 L1040 0 Z" fill="url(#navy)"/>
    </svg>

    <div class="brand">
      <div class="brand-name">Oakridge Interiors</div>
      <div class="brand-tagline">Trade Furniture Solutions</div>
    </div>

    <div class="details">
      <div class="person-name">DANIEL HARPER</div>
      <div class="person-title">Manager</div>
      <div class="address">Your Address, 2nd Ste<br>Maplefield, Ohio 4521, USA</div>
      <ul class="contacts">
        <li><svg class="contact-icon" viewBox="0 0 30 30"><rect width="30" height="30" fill="var(--gold)"/><path d="M10 7 l3 0 1 5 -2 1 c1 3 3 5 5 5 l1 -2 5 1 0 3 c-8 1 -14 -5 -13 -13z" fill="var(--navy-deep)"/></svg>123 456 7890</li>
        <li><svg class="contact-icon" viewBox="0 0 30 30"><rect width="30" height="30" fill="var(--gold)"/><rect x="10" y="6" width="10" height="6" fill="var(--navy-deep)"/><rect x="6" y="12" width="18" height="9" rx="1" fill="var(--navy-deep)"/><rect x="10" y="18" width="10" height="6" fill="var(--navy-deep)"/></svg>123 456 7890</li>
        <li><svg class="contact-icon" viewBox="0 0 30 30"><rect width="30" height="30" fill="var(--gold)"/><rect x="10" y="5" width="10" height="20" rx="2" fill="var(--navy-deep)"/><rect x="12" y="8" width="6" height="7" fill="var(--gold)"/></svg>123 456 7890</li>
        <li><svg class="contact-icon" viewBox="0 0 30 30"><rect width="30" height="30" fill="var(--gold)"/><rect x="6" y="9" width="18" height="12" fill="var(--navy-deep)"/><path d="M6 9 l9 7 9 -7" fill="none" stroke="var(--gold)" stroke-width="1.5"/></svg>your@yourcompany.com</li>
        <li><svg class="contact-icon" viewBox="0 0 30 30"><rect width="30" height="30" fill="var(--gold)"/><g fill="none" stroke="var(--navy-deep)" stroke-width="1.6"><circle cx="15" cy="15" r="9"/><ellipse cx="15" cy="15" rx="4" ry="9"/><path d="M6 15h18M8 10h14M8 20h14"/></g></svg>www.yourcompany.com</li>
      </ul>
    </div>
  </div>
</div>
</body>
</html>
```